Stage Design Company Business Card

We are looking to step up up our business card design for our team.

We are a Full service Design and Consultation company for Stage and TV with an emphasis in Theatrical Lighting.

We like our materials to be clean and modern with solid colors free of patterns and gradients. Our brand consists of 4 primary colors Purple, Black, Grey, and White. Provided is our Word Mark as well as our Symbol Logo.

We would like our cards to leave an impression beyond the information, show our attention to design and detail, and make our marks an easily recognized feature (together or apart) for our clients.

We need a warm approachable comfortable feel for some clients, and a professional flair for the board member type clients.

Attached are our brand elements, and our existing cards to give a sense of our style and a glipse at the information we provide on our cards.

Target Market(s)

broad client base from church leaders to high school teachers and architects.

Industry/Entity Type

Business

Contact Information for Business Card

We format our phone number with periods not parenthesis or dashes. Information will be edited for each of our team members, and team member specific cards are not part of this scope, but rather a template so to speak.

Font styles to use
Sans Serif

Colors
6b449b
ffffff
000000
333333
aaaaaa

Requirements
Must have
• Wordmark and logo mark present (does not need to exist on the same side of card)
• Brand Colors,
• Name, Phone, Email, Address.
• Unique choices that make someone stop and take a second look
Nice to have
• It would be nice to somehow convey what we DO, as our brand name does not lend itself to this, outside of an obvious tagline though.....
• social media if not crowded. all of our handles match (instagram, twitter, facebook)
Should not have
• "clipart"

```html
<!DOCTYPE html>
<html lang="en">
<head>
<meta charset="utf-8">
<title>Korve Entertainment Business Card</title>
<link href="https://fonts.googleapis.com/css2?family=Quicksand:wght@500&display=swap" rel="stylesheet">
<style>
  :root {
    --backdrop: #2b2b2d;
    --card-white: #ffffff;
    --brand-purple: #3b2470;
    --ink-black: #111111;
    --ink-grey: #aaaaaa;
    --text-light: #ffffff;
  }
  html, body {
    margin: 0;
    padding: 0;
    width: 1200px;
    height: 880px;
    overflow: hidden;
    background: var(--backdrop);
    font-family: "Quicksand", sans-serif;
  }
  .canvas {
    position: relative;
    width: 1200px;
    height: 880px;
  }
  .card {
    position: absolute;
    width: 520px;
    height: 298px;
    border-radius: 20px;
    overflow: hidden;
  }
  /* Front side */
  .card-front {
    left: 70px;
    top: 130px;
    background: var(--card-white);
    display: flex;
    align-items: center;
    justify-content: center;
  }
  .front-mark {
    display: flex;
    flex-direction: column;
    align-items: center;
    gap: 14px;
  }
  .mark-dot {
    width: 64px;
    height: 64px;
    border-radius: 50%;
    background: var(--brand-purple);
  }
  .wordmark {
    color: var(--ink-black);
    font-weight: 500;
    text-align: center;
    line-height: 1.4;
  }
  .wordmark-name {
    display: block;
    font-size: 34px;
    letter-spacing: 22px;
    margin-right: -22px;
  }
  .wordmark-sub {
    display: block;
    font-size: 9px;
    letter-spacing: 9px;
    margin-right: -9px;
  }
  /* Back side */
  .card-back {
    left: 610px;
    top: 452px;
    background: var(--brand-purple);
    color: var(--text-light);
  }
  .back-mark {
    position: absolute;
    left: 34px;
    top: 0;
    bottom: 0;
    display: flex;
    align-items: center;
  }
  .back-wordmark {
    font-weight: 500;
    font-size: 30px;
    letter-spacing: 6px;
    color: var(--text-light);
    writing-mode: vertical-rl;
    transform: rotate(180deg);
  }
  .contact {
    position: absolute;
    right: 36px;
    top: 44px;
    width: 270px;
    text-align: center;
    font-weight: 500;
  }
  .contact-name {
    font-size: 26px;
    letter-spacing: 1px;
    margin: 0;
    padding-bottom: 8px;
    border-bottom: 2px dotted var(--text-light);
    font-weight: 500;
  }
  .contact-phone,
  .contact-email {
    font-size: 20px;
    margin: 10px 0 0;
  }
  .contact-email {
    padding-bottom: 10px;
    border-bottom: 2px dotted var(--text-light);
    font-size: 18px;
  }
  .contact-address {
    font-style: normal;
    font-size: 17px;
    line-height: 1.35;
    margin-top: 12px;
    letter-spacing: 0.5px;
  }
</style>
</head>
<body>
  <main class="canvas">
    <section class="card card-front" aria-label="Card front">
      <div class="front-mark">
        <span class="mark-dot" aria-hidden="true"></span>
        <div class="wordmark">
          <span class="wordmark-name">KORVE</span>
          <span class="wordmark-sub">ENTERTAINMENT</span>
        </div>
      </div>
    </section>

    <section class="card card-back" aria-label="Card back">
      <div class="back-mark">
        <span class="back-wordmark">KORVE</span>
      </div>
      <div class="contact">
        <h1 class="contact-name">MARK T OLSEN</h1>
        <p class="contact-phone">480.555.0147</p>
        <p class="contact-email">mark@korve-e.com</p>
        <address class="contact-address">52 E OAK ST<br>TEMPE,AZ 85281</address>
      </div>
    </section>
  </main>
</body>
</html>
```